Coastal Learner Bureau business cards

Australian company about to start offering its services. We recruit international students to come to study English, vocational education and postgraduate courses in Australia. We help them find the institution and select the right city they want to come to Australia. We are a young, online oriented and supportive agency. Our clients are between 18 and 35 years old, mainly University students, young professionals or people with work experience. We provide much more information that any other agency offer. We administrate a Facebook group with more than 11.000 members that daily ask questions about general information when coming to Australia, while they are here and even after they leave the country

Target Market(s)

International students from South America, Central America and Europe

Industry/Entity Type

Student

Contact Information for Business Card

Tomas Bilbrea
Managing Director
tomas@kelvarin.com.au
www.kelvoria.com.au
+61 491058264
Melbourne, Australia

Font styles to use
Serif
Sans Serif

Colors

Designer to choose colors to be used in the design.

Requirements
Must have
• Horizontal design
• Standard business card size and shape. If font uses green or yellow colours, they will have to match the ones from the logo
Nice to have
• UPDATE: Use the contents of the green image to design one of the card sides. Use our logo in the background of that side as watermark.
• Passport image, or immigration stamps. A picture of the Yarra River (from Melbourne) would be cool as well.
Should not have
• Non-standard business card size and shape
• Not black as the background colour of any sides as we are not a VIP agency or a hight class service. We are orientes to young people and they like colours, pictures, something attractive.
• Vertical design
• NO YELLOW or BLACK AS THE BACKGROUND COLOUR OF ANY SIDE OF THE BIZ CARD

```html
<!DOCTYPE html>
<html lang="en">
<head>
<meta charset="utf-8">
<title>Coastal Learner Bureau business cards</title>
<link rel="stylesheet" href="https://fonts.googleapis.com/css2?family=Arimo:wght@400;700&display=swap">
<style>
  :root {
    --stage: #2e2e2e;
    --green: #1e7a45;
    --green-dark: #17613a;
    --gold: #e2b31c;
    --ink: #2a2a2a;
    --paper-light: #eadfae;
    --paper-dark: #cdb978;
    --page-light: #f7f4f6;
    --page-tint: #e9e2ec;
  }
  * { margin: 0; padding: 0; box-sizing: border-box; }
  html, body {
    width: 1200px; height: 997px; overflow: hidden;
    background: var(--stage);
    font-family: "Arimo", Arial, sans-serif;
  }
  .card {
    position: absolute; left: 250px;
    width: 700px; height: 400px;
    border-radius: 22px; overflow: hidden;
  }
  .card--back { top: 70px; }
  .card--front { top: 527px; }

  .stamp-field { position: absolute; inset: 0; }
  .card--back .stamp-field {
    background: radial-gradient(ellipse at 50% 45%, var(--paper-light), var(--paper-dark));
  }
  .card--front .stamp-field {
    background: linear-gradient(160deg, var(--page-light) 0%, var(--page-tint) 55%, var(--page-light) 100%);
  }

  .brand {
    position: absolute; display: flex; align-items: center; gap: 12px;
    color: var(--green); font-weight: 700;
  }
  .brand__dot { width: 22px; height: 22px; border-radius: 50%; background: var(--gold); }
  .card--back .brand { left: 0; right: 0; top: 160px; justify-content: center; font-size: 58px; }
  .card--front .brand { left: 200px; top: 70px; font-size: 52px; }

  .web {
    position: absolute; right: 34px; bottom: 34px;
    color: var(--green); font-weight: 700; font-size: 20px;
  }

  .rule { position: absolute; height: 2px; background: var(--green-dark); }
  .rule--top { left: 420px; right: 28px; top: 150px; }
  .rule--name { left: 36px; width: 340px; top: 218px; }

  .person { position: absolute; left: 36px; top: 186px; }
  .person__name { color: var(--green); font-weight: 700; font-size: 22px; letter-spacing: 0.5px; line-height: 26px; }
  .person__role { color: var(--ink); font-size: 18px; line-height: 22px; margin-top: 12px; }

  .company { position: absolute; right: 30px; top: 170px; text-align: right; color: var(--ink); font-size: 17px; line-height: 22px; }
  .company__name { color: var(--green); font-weight: 700; font-size: 18px; }

  .contacts { position: absolute; left: 36px; bottom: 30px; list-style: none; }
  .contacts li { display: flex; align-items: center; gap: 12px; color: var(--ink); font-size: 20px; margin-top: 10px; }
  .contacts svg { width: 24px; height: 24px; flex: none; }
</style>
</head>
<body>

<section class="card card--back" aria-label="Card back">
  <div class="stamp-field" role="img" aria-label="Aged passport page covered with immigration stamps, including an approved stamp"></div>
  <div class="brand"><span class="brand__dot"></span><span>Kelvoria</span></div>
  <p class="web">www.kelvoria.com.au</p>
</section>

<section class="card card--front" aria-label="Card front">
  <div class="stamp-field" role="img" aria-label="Light passport page with faint visa and immigration stamps"></div>
  <div class="brand"><span class="brand__dot"></span><span>Kelvoria</span></div>
  <div class="rule rule--top"></div>

  <div class="company">
    <p class="company__name">KELVORIA PVT LTD.</p>
    <p>28 Harlow Lane, Suite 412,</p>
    <p>Melbourne, Australia 3000</p>
  </div>

  <div class="person">
    <p class="person__name">TOMAS BILBREA</p>
    <p class="person__role">Managing Director</p>
  </div>
  <div class="rule rule--name"></div>

  <ul class="contacts">
    <li>
      <svg viewBox="0 0 24 24" aria-hidden="true"><circle cx="12" cy="12" r="12" fill="#1e7a45"/><path d="M8.5 6.5l2 2.2-1.2 1.6c.8 1.7 2.1 3 3.8 3.8l1.6-1.2 2.2 2-1.3 2c-4.6-.3-8.5-4.2-8.8-8.8z" fill="#fff"/></svg>
      <span>+61 491058264</span>
    </li>
    <li>
      <svg viewBox="0 0 24 24" aria-hidden="true"><circle cx="12" cy="12" r="12" fill="#1e7a45"/><rect x="6" y="8" width="12" height="8.5" rx="1" fill="#fff"/><path d="M6.5 8.5l5.5 4.2 5.5-4.2" stroke="#1e7a45" stroke-width="1.2" fill="none"/></svg>
      <span>tomas@kelvarin.com.au</span>
    </li>
  </ul>
</section>

</body>
</html>
```